Tolbek cards

I want a simple business card that pops.
Logo on one side.
On side two i want.
"Are you thinking about a new building on your property, or renovating an existing structure? Contact".....
Owners Name: Dale Whitacre
Owners Phone number: 610-555-0187
Address:4076 Copper Ridge RD, Millbrook, PA 17390
Committed to Quality, Service, and Integrity

```html
<!DOCTYPE html>
<html lang="en">
<head>
<meta charset="utf-8">
<title>Tolbek Builders LLC – Business Cards</title>
<link href="https://fonts.googleapis.com/css2?family=Archivo:wght@400;700;800;900&display=swap" rel="stylesheet">
<style>
  :root {
    --bg: #2a2a2a;
    --card: #f1f0ee;
    --brown: #4a3426;
    --tan: #a58c6e;
    --tan-text: #ad9479;
    --white: #ffffff;
  }
  * { margin: 0; padding: 0; box-sizing: border-box; }
  html, body { width: 1138px; height: 1200px; overflow: hidden; }
  body {
    background: var(--bg);
    font-family: "Archivo", Arial, sans-serif;
    color: var(--brown);
    position: relative;
  }
  .card {
    position: absolute;
    background: var(--card);
    border-radius: 16px;
    overflow: hidden;
    text-align: center;
  }
  .card--front { left: 185px; top: 302px; width: 377px; height: 624px; }
  .card--back  { left: 607px; top: 305px; width: 375px; height: 619px; }

  .brand-mark {
    position: absolute;
    background: var(--brown);
    left: 50%;
    transform: translateX(-50%);
  }
  .card--front .brand-mark { top: 150px; width: 130px; height: 130px; }
  .card--back .brand-mark  { top: 42px; width: 60px; height: 60px; }

  .brand-name {
    position: absolute;
    left: 0; right: 0;
    font-weight: 900;
    color: var(--brown);
    text-transform: uppercase;
    line-height: 1;
  }
  .card--front .brand-name { top: 455px; font-size: 52px; letter-spacing: 1px; }
  .card--front .brand-name span { display: block; font-size: 24px; font-weight: 800; letter-spacing: 9px; margin-top: 8px; padding-left: 9px; }
  .card--back .brand-name { top: 118px; font-size: 40px; letter-spacing: 1px; }
  .card--back .brand-name span { display: block; font-size: 15px; font-weight: 800; letter-spacing: 2px; margin-top: 6px; }

  .tagline {
    position: absolute;
    left: 0; right: 0;
    font-size: 15.5px;
    font-weight: 400;
    color: var(--brown);
  }
  .card--front .tagline { top: 571px; }
  .card--back .tagline  { top: 566px; }

  .pitch-band {
    position: absolute;
    top: 235px; left: 0; right: 0;
    height: 122px;
    background: var(--brown);
    color: var(--white);
    font-weight: 700;
    font-size: 16.5px;
    line-height: 22.5px;
    padding-top: 12px;
    text-transform: uppercase;
  }
  .contact-pill {
    position: absolute;
    top: 347px;
    left: 50%;
    transform: translateX(-50%);
    width: 126px; height: 21px;
    border-radius: 11px;
    background: var(--tan);
    color: var(--white);
    font-weight: 700;
    font-size: 15px;
    line-height: 21px;
  }
  .owner-name {
    position: absolute;
    top: 410px; left: 0; right: 0;
    font-size: 24px;
    font-weight: 700;
    text-transform: uppercase;
  }
  .owner-name .surname { color: var(--tan); }
  .owner-phone {
    position: absolute;
    top: 443px; left: 0; right: 0;
    font-size: 16px;
    font-weight: 700;
  }
  .owner-address {
    position: absolute;
    top: 466px; left: 0; right: 0;
    font-size: 15px;
    line-height: 21px;
    color: var(--tan-text);
  }
  .divider {
    position: absolute;
    top: 547px; left: 39px; right: 39px;
    height: 1px;
    background: var(--tan);
  }
</style>
</head>
<body>
  <section class="card card--front">
    <div class="brand-mark"></div>
    <div class="brand-name">Tolbek<span>Builders LLC</span></div>
    <p class="tagline">Committed to Quality, Service &amp; Integrity</p>
  </section>

  <section class="card card--back">
    <div class="brand-mark"></div>
    <div class="brand-name">Tolbek<span>Builders LLC</span></div>
    <div class="pitch-band">
      Are you thinking about a<br>new building on your<br>property, or renovating<br>an existing structure?
    </div>
    <div class="contact-pill">CONTACT</div>
    <p class="owner-name">Dale <span class="surname">Whitacre</span></p>
    <p class="owner-phone">Call: 610-555-0187</p>
    <p class="owner-address">Add.: 4076 Copper Ridge RD,<br>Millbrook, PA 17390</p>
    <div class="divider"></div>
    <p class="tagline">Committed to Quality, Service &amp; Integrity</p>
  </section>
</body>
</html>
```